Business Card Design Project

Business card based on attached logo

Todd Merrick
Todd@lorvantest.com
877-514-9073 ext. 318
Www.LorvanTest.com

Industry/Entity Type

Business

```html
<!DOCTYPE html>
<html lang="en">
<head>
<meta charset="utf-8">
<title>LorvanTest Business Card Concepts</title>
<link href="https://fonts.googleapis.com/css2?family=Montserrat:ital,wght@0,400;0,600;0,800;1,700&display=swap" rel="stylesheet">
<style>
  :root {
    --board: #d8cdc2;
    --label: #1c1410;
    --card-white: #ffffff;
    --brand-red: #e0262c;
    --name-red: #8e1c1f;
    --ink: #111111;
    --text-grey: #444444;
  }
  * { margin: 0; padding: 0; box-sizing: border-box; }
  html, body {
    width: 1200px; height: 788px; overflow: hidden;
    background: var(--board);
    font-family: "Montserrat", Arial, sans-serif;
  }
  .board { position: relative; width: 1200px; height: 788px; }
  .view-label {
    position: absolute; width: 525px; text-align: center;
    font-size: 20px; font-weight: 400; color: var(--label);
  }
  .card {
    position: absolute; width: 525px; height: 300px; border-radius: 20px;
    overflow: hidden; background: var(--card-white);
    box-shadow: 0 4px 12px rgba(0,0,0,.25);
  }
  .card--front { left: 54px; top: 74px; }
  .card--back-white { left: 622px; top: 74px; }
  .card--back-red { left: 54px; top: 445px; background: linear-gradient(#d8262c, #a51b21); }
  .card--back-grey { left: 622px; top: 445px; background: linear-gradient(#fafafa, #e4e4e4); }

  .wordmark {
    position: absolute; display: flex; align-items: center; gap: 10px;
    font-weight: 800; color: var(--ink); letter-spacing: -1px; white-space: nowrap;
  }
  .wordmark__square { width: 22px; height: 22px; background: var(--brand-red); flex: none; }
  .card--back-red .wordmark { color: #ffffff; }
  .card--back-red .wordmark__square { background: var(--ink); }

  .card--front .wordmark { left: 30px; top: 104px; font-size: 38px; gap: 8px; }
  .card--front .wordmark__square { width: 18px; height: 18px; }
  .card--back-white .wordmark,
  .card--back-red .wordmark { left: 0; right: 0; justify-content: center; top: 100px; font-size: 54px; }

  .contact-name { position: absolute; left: 299px; top: 80px; font-size: 17px; font-weight: 600; color: var(--name-red); }
  .contact-phone { position: absolute; left: 299px; top: 105px; font-size: 12.5px; color: var(--text-grey); white-space: nowrap; }
  .contact-phone b, .footer-line b { font-style: italic; font-weight: 700; }
  .contact-phone b { color: var(--brand-red); margin-right: 3px; }

  .front-band { position: absolute; left: 0; bottom: 0; width: 525px; height: 60px; }
  .footer-lines { position: absolute; left: 299px; top: 257px; font-size: 12.5px; line-height: 17px; color: #ffffff; white-space: nowrap; }

  .web-address { position: absolute; left: 0; right: 0; top: 250px; text-align: center; font-size: 17px; color: var(--text-grey); }
  .card--back-red .web-address { color: #ffffff; }

  .raised-panel {
    position: absolute; left: 81px; top: 82px; width: 360px; height: 128px;
    background: linear-gradient(#ffffff, #f0f0f0);
    box-shadow: 0 8px 10px rgba(0,0,0,.22);
  }
  .raised-panel .wordmark { left: 0; right: 0; justify-content: center; top: 40px; font-size: 38px; }
  .raised-panel .wordmark__square { width: 16px; height: 16px; }
</style>
</head>
<body>
<main class="board">
  <p class="view-label" style="left:54px;top:34px">Front</p>
  <p class="view-label" style="left:622px;top:34px">Back - 1</p>
  <p class="view-label" style="left:54px;top:405px">Back - 2</p>
  <p class="view-label" style="left:622px;top:405px">Back - 3</p>

  <section class="card card--front" aria-label="Card front">
    <div class="wordmark"><span>LorvanTest</span><span class="wordmark__square"></span></div>
    <p class="contact-name">Todd Merrick</p>
    <p class="contact-phone"><b>p :</b> 877-514-9073 ext. 318</p>
    <svg class="front-band" viewBox="0 0 525 60" aria-hidden="true">
      <polygon points="0,26 262,26 250,43 0,43" fill="#111"/>
      <polygon points="0,46 248,46 240,60 0,60" fill="#e0262c"/>
      <polygon points="286,0 525,0 525,60 248,60" fill="#e0262c"/>
    </svg>
    <div class="footer-lines">
      <p class="footer-line"><b>email</b> Todd@lorvantest.com</p>
      <p class="footer-line"><b>web</b> www.LorvanTest.com</p>
    </div>
  </section>

  <section class="card card--back-white" aria-label="Card back, white">
    <div class="wordmark"><span>LorvanTest</span><span class="wordmark__square"></span></div>
    <p class="web-address">www.LorvanTest.com</p>
  </section>

  <section class="card card--back-red" aria-label="Card back, red">
    <div class="wordmark"><span>LorvanTest</span><span class="wordmark__square"></span></div>
    <p class="web-address">www.LorvanTest.com</p>
  </section>

  <section class="card card--back-grey" aria-label="Card back, grey with raised panel">
    <div class="raised-panel">
      <div class="wordmark"><span>LorvanTest</span><span class="wordmark__square"></span></div>
    </div>
    <p class="web-address">www.LorvanTest.com</p>
  </section>
</main>
</body>
</html>
```